Tech business card design

We need an amazing business card design for our new business 'Pexla' a marketing tech startup based in Sydney, Australia. We provide an online marketplace for businesses to search and buy advertising media, connect with service providers and learn more about marketing. We wish to communicate 'cool tech', reliability and professionalism and design based around our logo.

Target Market(s)

Business Owners

Contact Information for Business Card

Name
Position
Email Address
Website
Phone Number

Font styles to use
Other font styles liked:
• Avenir & Avenir Next

Colors

Designer to choose colors to be used in the design.

```html
<!DOCTYPE html>
<html lang="en">
<head>
<meta charset="utf-8">
<title>Pexla Business Card</title>
<link rel="stylesheet" href="https://fonts.googleapis.com/css2?family=Montserrat:wght@800&family=Mulish:wght@300;400&display=swap">
<style>
  :root {
    --bg: #e6e6e6;
    --navy: #1f1d45;
    --navy-card: #2b2955;
    --navy-soft: #34325f;
    --white: #ffffff;
    --ink: #1f1d45;
    --shadow: 0 10px 24px rgba(0,0,0,0.18);
  }
  * { box-sizing: border-box; margin: 0; padding: 0; }
  html, body {
    width: 1200px; height: 900px; overflow: hidden;
    background: var(--bg);
    font-family: "Mulish", sans-serif;
  }
  .canvas { position: relative; width: 1200px; height: 900px; }

  .card {
    position: absolute;
    width: 560px; height: 342px;
    box-shadow: var(--shadow);
    overflow: hidden;
  }

  /* Back side */
  .card-back { left: 90px; top: 90px; background: var(--navy-card); }
  .card-back .pattern {
    position: absolute; inset: 0;
    background: linear-gradient(135deg, var(--navy-soft) 0%, var(--navy-card) 55%, #24224b 100%);
  }
  .card-back .wordmark {
    position: absolute; left: 300px; top: 128px;
    font-family: "Montserrat", sans-serif; font-weight: 800;
    font-size: 46px; letter-spacing: -1px;
    color: var(--white); line-height: 1;
  }
  .card-back .web {
    position: absolute; left: 0; right: 0; top: 236px;
    text-align: center; padding-left: 80px;
    font-weight: 300; font-size: 21px; letter-spacing: 0.5px;
    color: var(--white);
  }

  /* Front side */
  .card-front { left: 550px; top: 468px; background: var(--white); }
  .card-front .band {
    position: absolute; left: 0; right: 0; bottom: 0; height: 30px;
    background: var(--navy);
  }
  .card-front .wordmark {
    position: absolute; left: 150px; top: 44px;
    font-family: "Montserrat", sans-serif; font-weight: 800;
    font-size: 104px; letter-spacing: -4px;
    color: var(--ink); line-height: 1;
  }
  .card-front .identity {
    position: absolute; right: 300px; top: 184px;
    text-align: right; color: var(--ink);
  }
  .identity .name {
    font-family: "Montserrat", sans-serif; font-weight: 800;
    font-size: 21px; line-height: 1.15;
  }
  .identity .role { font-weight: 300; font-size: 21px; line-height: 1.15; }

  .card-front .divider {
    position: absolute; left: 276px; top: 176px;
    width: 1.5px; height: 66px; background: var(--ink);
  }
  .contact-list {
    position: absolute; left: 292px; top: 174px;
    list-style: none; color: var(--ink);
  }
  .contact-list li {
    display: flex; align-items: center; gap: 8px;
    font-weight: 300; font-size: 15.5px; line-height: 23px;
  }
  .contact-list svg { width: 13px; height: 13px; flex: none; }
</style>
</head>
<body>
<main class="canvas">

  <section class="card card-back" aria-label="Business card, back">
    <div class="pattern" role="img" aria-label="Repeating tone-on-tone brand pattern in deep navy"></div>
    <div class="wordmark">Pexla</div>
    <p class="web">www.pexlamedia.com.au</p>
  </section>

  <section class="card card-front" aria-label="Business card, front">
    <div class="wordmark">Pexla</div>

    <div class="identity">
      <p class="name">Marcus Reed</p>
      <p class="role">Founder, Director</p>
    </div>

    <div class="divider"></div>

    <ul class="contact-list">
      <li>
        <svg viewBox="0 0 16 16" aria-hidden="true"><path fill="#1f1d45" d="M3.6 1.5l2.2 2.6-1.2 1.6c.9 2.1 2.5 3.7 4.6 4.6l1.6-1.2 2.6 2.2-1.3 2.2C6.6 14.8 1.2 9.4 1.3 2.8z"/></svg>
        <span>+61 (0)412 555 019</span>
      </li>
      <li>
        <svg viewBox="0 0 16 16" aria-hidden="true"><rect x="1" y="3" width="14" height="10" fill="#1f1d45"/><path d="M1.5 3.5L8 9l6.5-5.5" fill="none" stroke="#fff" stroke-width="1.4"/></svg>
        <span>marcus@pexlamedia.com.au</span>
      </li>
      <li>
        <svg viewBox="0 0 16 16" aria-hidden="true"><g fill="none" stroke="#1f1d45" stroke-width="1.4"><circle cx="8" cy="8" r="6.3"/><ellipse cx="8" cy="8" rx="2.7" ry="6.3"/><path d="M1.7 8h12.6M2.6 5h10.8M2.6 11h10.8"/></g></svg>
        <span>www.pexlamedia.com.au</span>
      </li>
    </ul>

    <div class="band"></div>
  </section>

</main>
</body>
</html>
```